Small Business Broker Business Card Design

A business card design for a small business brokerage, which is a financial service, not unlike real estate brokerage, but for small businesses such as laundromats, pizza shops, restaurants, cleaners etc. The designs should all be simple, more conservative in nature, using the colors and font of the logo. Again, think real estate Brokerage as a business context
Contact Information for Business Card
Name: Glen R. Harlow. Title: Small Business Advisor. Email: g.harlow@bayfieldcapitalworks.example. Mobile: (555) 274-3918. Office: (555) 806-2147. www.bayfieldcapitalworks.example

```html
<!DOCTYPE html>
<html lang="en">
<head>
<meta charset="utf-8">
<title>Bayfield Capital Works – Business Card</title>
<link rel="stylesheet" href="https://fonts.googleapis.com/css2?family=Montserrat:wght@600;700&family=Open+Sans:wght@400;600&display=swap">
<style>
  :root {
    --stage: #242424;
    --card: #1b1c1e;
    --green: #8dc63f;
    --blue: #1f4a8a;
    --white: #f2f2f2;
    --emboss: #2e2f32;
    --emboss-light: #6a6b6e;
  }
  * { box-sizing: border-box; margin: 0; padding: 0; }
  html, body {
    width: 1200px; height: 780px; overflow: hidden;
    background: var(--stage);
  }
  .stage {
    width: 1200px; height: 780px;
    display: flex; align-items: center; justify-content: center; gap: 32px;
  }
  .card {
    position: relative;
    width: 560px; height: 320px;
    background: var(--card);
    border-radius: 22px;
    border-bottom: 5px solid var(--green);
    border-left: 2px solid var(--green);
    overflow: hidden;
  }

  /* Back side */
  .card--back .brand {
    position: absolute; left: 0; right: 0; top: 118px;
    text-align: center;
  }
  .card--back .brand-mark {
    display: inline-block; width: 22px; height: 22px;
    background: var(--emboss-light); margin-bottom: 16px;
  }
  .card--back .brand-name {
    font-family: "Montserrat", sans-serif; font-weight: 700;
    font-size: 25px; letter-spacing: 1px; text-transform: uppercase;
    color: var(--emboss-light);
  }
  .card--back .brand-tagline {
    margin-top: 6px;
    font-family: "Montserrat", sans-serif; font-weight: 700;
    font-size: 11.5px; letter-spacing: 2.6px; text-transform: uppercase;
    color: var(--emboss-light);
  }

  /* Front side */
  .card--front .brand {
    position: absolute; right: 24px; top: 40px; width: 270px;
    text-align: center;
  }
  .card--front .brand-name {
    font-family: "Montserrat", sans-serif; font-weight: 700;
    font-size: 14.5px; letter-spacing: .4px; text-transform: uppercase;
    color: var(--blue);
  }
  .card--front .brand-tagline {
    margin-top: 3px;
    font-family: "Montserrat", sans-serif; font-weight: 700;
    font-size: 7.2px; letter-spacing: 1.1px; text-transform: uppercase;
    color: var(--green);
  }
  .identity {
    position: absolute; left: 0; top: 176px;
    padding-left: 34px;
  }
  .identity::before {
    content: ""; position: absolute; left: 0; top: 20px;
    width: 16px; height: 36px; background: var(--green);
  }
  .person-name {
    font-family: "Montserrat", sans-serif; font-weight: 700;
    font-size: 25px; letter-spacing: .5px; text-transform: uppercase;
    color: var(--blue); line-height: 1.1;
  }
  .person-title {
    font-family: "Open Sans", sans-serif; font-weight: 400;
    font-size: 16px; color: var(--green); margin-top: 2px;
  }
  .contacts {
    position: absolute; left: 48px; top: 242px;
    list-style: none;
    font-family: "Open Sans", sans-serif; font-size: 12.5px; color: var(--white);
  }
  .contacts li { display: flex; align-items: center; gap: 7px; line-height: 17px; }
  .contacts svg { width: 11px; height: 11px; flex: none; }
</style>
</head>
<body>
<main class="stage">

  <section class="card card--back" aria-label="Card back">
    <div class="brand">
      <span class="brand-mark"></span>
      <div class="brand-name">Bayfield Capital Works, Inc</div>
      <div class="brand-tagline">Confidently buy or sell a local business today</div>
    </div>
  </section>

  <section class="card card--front" aria-label="Card front">
    <div class="brand">
      <div class="brand-name">Bayfield Capital Works, Inc</div>
      <div class="brand-tagline">Confidently buy or sell a local business today</div>
    </div>

    <div class="identity">
      <h1 class="person-name">Glen R. Harlow</h1>
      <p class="person-title">Small Business Advisor</p>
    </div>

    <ul class="contacts">
      <li>
        <svg viewBox="0 0 12 12" aria-hidden="true"><rect x="3" y="0.5" width="6" height="11" rx="1" fill="none" stroke="#8dc63f" stroke-width="1.2"/><circle cx="6" cy="9.6" r=".7" fill="#8dc63f"/></svg>
        (555) 274-3918
      </li>
      <li>
        <svg viewBox="0 0 12 12" aria-hidden="true"><path d="M1 4.5C1 2.5 11 2.5 11 4.5L9.5 5.5 8.5 4H3.5L2.5 5.5Z" fill="#8dc63f"/><rect x="2.5" y="6" width="7" height="5" rx="1" fill="#8dc63f"/></svg>
        (555) 806-2147
      </li>
      <li>
        <svg viewBox="0 0 12 12" aria-hidden="true"><rect x="0.8" y="2.5" width="10.4" height="7.5" fill="none" stroke="#8dc63f" stroke-width="1.2"/><path d="M1 3l5 4 5-4" fill="none" stroke="#8dc63f" stroke-width="1.2"/></svg>
        g.harlow@bayfieldcapitalworks.example
      </li>
      <li>
        <svg viewBox="0 0 12 12" aria-hidden="true"><circle cx="6" cy="6" r="5" fill="none" stroke="#8dc63f" stroke-width="1.2"/><path d="M1 6h10M6 1c-2.5 3-2.5 7 0 10M6 1c2.5 3 2.5 7 0 10" fill="none" stroke="#8dc63f" stroke-width="1"/></svg>
        www.bayfieldcapitalworks.example
      </li>
    </ul>
  </section>

</main>
</body>
</html>
```